TalkHarbor - Language Coaching Services

Sleek, innovative, trendy design for Language Coaching business.

TalkHarbor is a new UK based company that provides Language Coaching services. We offer highly personalized on-line and face to face language courses. We also impart learning techniques workshops based on the latest neuroscience research for second-language acquisition.

Target Market(s)

See attached info

Industry/Entity Type

Consulting

Contact Information for Business Card

TalkHarbor
DaniaKV@talkharbor.co.uk
TalkHarbor.co.uk
London, UK

Font styles to use
Sans Serif

```html
<!DOCTYPE html>
<html lang="en">
<head>
<meta charset="utf-8">
<title>TalkHarbor Business Card</title>
<link href="https://fonts.googleapis.com/css2?family=Roboto:wght@400;500&display=swap" rel="stylesheet">
<style>
  :root {
    --page-bg: #e6e6e6;
    --card-white: #ffffff;
    --card-dark: #1c1d1f;
    --brand-blue: #0a8fc8;
    --blue-bright: #12b4ea;
    --blue-deep: #005a8c;
    --text-light: #ffffff;
    --text-muted: #e2e2e2;
  }
  * { margin: 0; padding: 0; box-sizing: border-box; }
  html, body {
    width: 1125px; height: 1200px; overflow: hidden;
    background: var(--page-bg);
    font-family: "Roboto", sans-serif;
  }
  .card {
    position: absolute; left: 150px;
    width: 825px; height: 471px;
    border-radius: 22px; overflow: hidden;
  }
  .card-front { top: 98px; background: var(--card-white); }
  .card-back { top: 631px; background: var(--card-dark); }
  .card-art { position: absolute; inset: 0; }

  .brand-mark {
    position: absolute; left: 162px; top: 64px;
    width: 124px; height: 124px; border-radius: 50%;
    border: 9px solid var(--brand-blue);
  }
  .brand-name {
    position: absolute; left: 64px; top: 190px;
    font-size: 44px; font-weight: 400; letter-spacing: 1px;
    color: var(--brand-blue); line-height: 1;
  }

  .contact-block {
    position: absolute; right: 42px; top: 272px;
    text-align: right; color: var(--text-light);
  }
  .person-name { font-size: 29px; font-weight: 500; line-height: 1.05; }
  .person-role { font-size: 20px; font-weight: 400; color: var(--text-muted); margin-bottom: 20px; }
  .contact-line {
    display: flex; justify-content: flex-end; align-items: center; gap: 12px;
    font-size: 19px; line-height: 27px; color: var(--text-muted);
  }
  .contact-line svg { width: 18px; height: 18px; flex: none; }

  .back-mark {
    position: absolute; left: 281px; top: 92px;
    width: 264px; height: 264px; border-radius: 50%;
    border: 14px solid var(--brand-blue);
    display: flex; align-items: center; justify-content: center;
  }
  .back-mark-name {
    font-size: 30px; font-weight: 400; color: var(--brand-blue); letter-spacing: 1px;
  }
  .back-url {
    position: absolute; left: 0; right: 0; top: 402px;
    text-align: center; font-size: 20px; letter-spacing: 7px;
    color: var(--text-muted);
  }
</style>
</head>
<body>

<section class="card card-front">
  <svg class="card-art" viewBox="0 0 825 471" aria-hidden="true">
    <defs>
      <radialGradient id="swoosh-fill" cx="0.55" cy="0.85" r="0.6">
        <stop offset="0" stop-color="var(--blue-bright)"/>
        <stop offset="1" stop-color="var(--blue-deep)"/>
      </radialGradient>
    </defs>
    <path class="swoosh-band" d="M0,345 C40,410 170,412 310,362 C470,305 620,210 825,55 V471 H0 Z" fill="url(#swoosh-fill)"/>
    <path class="swoosh-line" d="M0,358 C45,418 175,420 315,372 C470,318 610,235 706,168" fill="none" stroke="#fff" stroke-width="2"/>
    <polygon class="swoosh-arrow" points="730,148 698,160 714,178" fill="#fff" opacity="0.9"/>
  </svg>

  <div class="brand-mark"></div>
  <div class="brand-name">TALKHARBOR</div>

  <div class="contact-block">
    <div class="person-name">OWEN MARLOW</div>
    <div class="person-role">CEO/FOUNDER</div>
    <div class="contact-line">620 555 0148
      <svg viewBox="0 0 18 18"><rect x="4" y="1" width="10" height="16" rx="2" fill="none" stroke="#fff" stroke-width="1.6"/><rect x="7.5" y="13.5" width="3" height="1.5" fill="#fff"/></svg>
    </div>
    <div class="contact-line">info@talkharbor.co.uk
      <svg viewBox="0 0 18 18"><rect x="1" y="4" width="16" height="11" rx="1" fill="#fff"/><path d="M1.5,4.5 L9,10.5 L16.5,4.5" fill="none" stroke="#0a6fa3" stroke-width="1.3"/></svg>
    </div>
    <div class="contact-line">www.talkharbor.co.uk
      <svg viewBox="0 0 18 18"><circle cx="9" cy="9" r="8" fill="#fff"/><ellipse cx="9" cy="9" rx="3.5" ry="8" fill="none" stroke="#0a6fa3" stroke-width="1.1"/><line x1="1" y1="9" x2="17" y2="9" stroke="#0a6fa3" stroke-width="1.1"/></svg>
    </div>
  </div>
</section>

<section class="card card-back">
  <div class="back-mark"><span class="back-mark-name">TALKHARBOR</span></div>
  <div class="back-url">www.talkharbor.co.uk</div>
</section>

</body>
</html>
```